Letterhead for a German Distribution/Manufacturing Company

We need a professional Letterhead in a unique Design.
not to playful.
The Letterhead has to show show that we are a international company with headquater in Germany.
all details like adress, Vat Tax Number, Bank Accout, Eori, email, Company number has to be on the Letterhead.
for example use: VAT TAX DE5470318 Bank Account: Kestrel Bank IBAN DE412058731ß204683 Swift: MORV0417352 EORI 3150428697 Company Number: HRB 51806 Adress: VOLMINTA UG Ahornweg 7 Postal Code 06384 City Eichental Country: Germany Email: info@volminta-example.com
the design can be colored but doesnt have to be
Industry/Entity Type
Manufacturing and international distribution
Requirements
Must have
- show that we are a international company with headquater in Germany. our company infos and logo

```html
<!DOCTYPE html>
<html lang="en">
<head>
<meta charset="utf-8">
<title>VOLMINTA Letterhead</title>
<link href="https://fonts.googleapis.com/css2?family=Lato:wght@400;700&family=Tangerine:wght@700&display=swap" rel="stylesheet">
<style>
  :root {
    --backdrop: #dcdcdc;
    --paper: #ffffff;
    --ink: #3a3a3a;
    --ink-strong: #111111;
    --brand: #3d3d3d;
  }
  * { margin: 0; padding: 0; box-sizing: border-box; }
  html, body {
    width: 1200px; height: 874px; overflow: hidden;
    background: var(--backdrop);
  }
  .canvas {
    position: relative; width: 1200px; height: 874px;
    display: flex; align-items: center; justify-content: center;
  }
  .letterhead {
    width: 594px; height: 840px;
    background: var(--paper);
    box-shadow: 0 2px 10px rgba(0,0,0,0.12);
    padding: 62px 58px 48px 64px;
    font-family: 'Lato', sans-serif;
    color: var(--ink);
    display: flex; flex-direction: column;
  }
  .brand {
    display: flex; align-items: center; gap: 10px;
    margin-bottom: 68px;
  }
  .brand-mark { width: 30px; height: 30px; flex: none; }
  .brand-name {
    font-size: 30px; font-weight: 400; letter-spacing: 1px;
    color: var(--brand);
  }
  .meta { font-size: 11px; line-height: 1.3; }
  .meta-date { margin-bottom: 12px; }
  .recipient { margin-bottom: 12px; }
  .salutation {
    font-size: 12.5px; font-weight: 700; color: var(--ink-strong);
    margin: 4px 0 12px;
  }
  .body-copy p {
    font-size: 10.6px; line-height: 1.32; margin-bottom: 13px;
  }
  .closing { font-size: 11px; margin-top: 8px; }
  .signature {
    font-family: 'Tangerine', cursive;
    font-size: 44px; font-weight: 700; color: var(--ink-strong);
    margin: 0 0 0 42px; line-height: 1.1;
  }
  .company-details {
    margin-top: 30px;
    font-size: 9.6px; line-height: 1.35; color: var(--ink-strong);
  }
</style>
</head>
<body>
<main class="canvas">
  <article class="letterhead">
    <header class="brand">
      <svg class="brand-mark" viewBox="0 0 30 30" aria-hidden="true">
        <circle cx="15" cy="15" r="13" fill="var(--brand)"/>
      </svg>
      <span class="brand-name">VOLMINTA</span>
    </header>

    <section class="meta">
      <p class="meta-date">January-03-2020</p>
      <p class="recipient">Mr. Jonas Weller<br>President</p>
      <p class="recipient">Harbor Line Corporation<br>48 Harbor Street, Suite# 10<br>City, State, 120023</p>
    </section>

    <p class="salutation">Dear Mr. Jonas</p>

    <section class="body-copy">
      <p>Lorem ipsum dolor sit amet, consectetur adipisicing elit, sed do eiusmod tempor incididunt ut labore et dolore magna aliqua. Ut enim ad minim veniam, quis nostrud exercitation ullamco laboris nisi ut aliquip ex ea commodo consequat. Duis aute irure dolor in reprehenderit in voluptate velit esse cillum dolore eu fugiat nulla pariatur.</p>
      <p>Lorem ipsum dolor sit amet, consectetur adipisicing elit, sed do eiusmod tempor incididunt ut labore et dolore magna aliqua. Ut enim ad minim veniam, quis nostrud exercitation ullamco laboris nisi ut aliquip ex ea commodo consequat. Duis aute irure dolor in reprehenderit in voluptate velit esse cillum dolore eu fugiat nulla pariatur.</p>
      <p>Lorem ipsum dolor sit amet, consectetur adipisicing elit, sed do eiusmod tempor incididunt ut labore et dolore magna aliqua. Ut enim ad minim veniam, quis nostrud exercitation ullamco laboris nisi ut aliquip ex ea commodo consequat.</p>
      <p>Excepteur sint occaecat cupidatat non proident, sunt in culpa qui officia deserunt mollit anim id est laborum. re et dolore magnam aliquam quaerat voluptatem.</p>
    </section>

    <p class="closing">Regards</p>
    <p class="signature">Daniel Hartwig</p>

    <footer class="company-details">
      <p>VAT TAX DE5470318</p>
      <p>Bank Account: Kestrel Bank IBAN DE412058731ß204683 Swift: MORV0417352</p>
      <p>EORI 3150428697</p>
      <p>Company Number: HRB 51806</p>
      <p>Adress: VOLMINTA UG Ahornweg 7 Postal Code 06384 City Eichental Country</p>
      <p>Germany Email: info@volminta-example.com</p>
    </footer>
  </article>
</main>
</body>
</html>
```